Manifesto

I want a manifesto with the following five manifestos for our Not for Profit

- We are a For-purpose organisation
- Every service we offer is free
- Every product we sell funds our services
- Every financial transaction is transparent
- Our service is for the greater good
- Our purpose is always to serve the people
- We are a for purpose organisation

Its to go with this website logo/look/feel www.brightharbour.co.nz

Two attachments:

1. I quite like this look/feel of a manifesto (see attached), I want something clean, professional but I also quite like either Retro modern look feel also like a fresh, and uplifting as its for sick people coming to see us and our funds where anyone buys a product are used for helping those who are sick with healing......so needs something conveyed that is fresh, uplifing yet professional.
2. This attachment is how I wrote this down when inspired of how I wanted Bright Harbour to operate. This is our values chart. It has to say

Also check out our website for our logo, look etc.. it doesnt have to be the same but red somewhere would link back to logo. www.brightharbour.co.nz .

Industry/Entity Type

Financial

```html
<!DOCTYPE html>
<html lang="en">
<head>
<meta charset="utf-8">
<title>Bright Harbour Manifesto</title>
<link rel="stylesheet" href="https://fonts.googleapis.com/css2?family=Alfa+Slab+One&family=Roboto+Slab:wght@700;800;900&family=Lobster&family=Lobster+Two:ital,wght@1,700&display=swap">
<style>
  :root {
    --backdrop: #e6e6e6;
    --poster-red: #94001c;
    --poster-edge: #5a0010;
    --ink-dark: #4c0412;
    --ink-light: #ffffff;
    --ink-shadow: #3a000b;
  }
  * { margin: 0; padding: 0; box-sizing: border-box; }
  html, body {
    width: 1200px;
    height: 1000px;
    overflow: hidden;
    background: var(--backdrop);
  }
  .poster {
    position: absolute;
    left: 287px;
    top: 53px;
    width: 628px;
    height: 889px;
    background: radial-gradient(ellipse at 50% 45%, var(--poster-red) 55%, var(--poster-edge) 120%);
    overflow: hidden;
  }
  .line {
    position: absolute;
    left: 23px;
    width: 582px;
    line-height: 1;
    white-space: nowrap;
    text-align: justify;
    text-align-last: justify;
  }
  .dark { color: var(--ink-dark); }
  .light {
    color: var(--ink-light);
    text-shadow: 2px 2px 0 var(--ink-shadow);
  }
  .slab-display { font-family: "Alfa Slab One", "Roboto Slab", serif; }
  .slab { font-family: "Roboto Slab", serif; font-weight: 900; }
  .script { font-family: "Lobster", cursive; }
  .script-italic { font-family: "Lobster Two", cursive; font-style: italic; font-weight: 700; }

  .headline-open { top: 24px; font-size: 104px; }
  .pair { display: flex; justify-content: space-between; align-items: baseline; text-align: left; text-align-last: auto; }
  .pair-top { top: 134px; }
  .pair-top .slab { font-size: 38px; letter-spacing: 0.5px; }
  .pair-top .script-italic { font-size: 31px; }
  .pair-bottom { top: 177px; }
  .pair-bottom .slab { font-size: 32px; }
  .pair-bottom .script-italic { font-size: 33px; }
  .product { top: 224px; font-size: 58px; }
  .product-funds { top: 290px; font-size: 33px; font-weight: 800; }
  .financial { top: 352px; font-size: 38px; letter-spacing: 8px; }
  .transparent { top: 400px; font-size: 25px; font-weight: 800; letter-spacing: 6px; }
  .service-is { top: 446px; font-size: 58px; letter-spacing: 3px; }
  .greater-good { top: 500px; font-size: 56px; letter-spacing: 1px; }
  .purpose-is { top: 576px; font-size: 56px; letter-spacing: 3px; }
  .serve-people { top: 636px; font-size: 50px; }
  .closing { top: 714px; font-size: 38px; }
  .closing-word { top: 752px; font-size: 104px; }
</style>
</head>
<body>
  <main class="poster" aria-label="Bright Harbour manifesto">
    <p class="line dark slab-display headline-open">WE ARE A</p>
    <p class="line pair pair-top">
      <span class="light slab">FOR PURPOSE</span>
      <span class="light script-italic">EveryService</span>
    </p>
    <p class="line pair pair-bottom">
      <span class="dark slab">ORGANISATION</span>
      <span class="dark script-italic">we offer is free</span>
    </p>
    <p class="line light slab product">EVERY PRODUCT</p>
    <p class="line dark slab product-funds">we sell funds our services</p>
    <p class="line light slab financial">EVERY FINANCIAL</p>
    <p class="line dark slab transparent">transaction is transparent</p>
    <p class="line dark slab service-is">OUR SERVICE IS</p>
    <p class="line light script-italic greater-good">for the greater good</p>
    <p class="line dark slab purpose-is">OUR PURPOSE IS</p>
    <p class="line light script serve-people">always to serve the people</p>
    <p class="line dark slab closing">WE ARE A FOR PURPOSE</p>
    <p class="line light script closing-word">organisation</p>
  </main>
</body>
</html>
```